Harbor Crest Holdings Corporate Showcase

Provide an attractive Corporate Website for a boutique Investment Company to showcase our activities and corporate interests.

Our Company works across a number of Sectors including

Real Estate
E-Commerce
Healthcare
Beauty & Personal Care
Technology
Resources

Lets keep the personality

Modern
Global
Sophisticated
Calm
Interesting

Lets keep the pages with MINIMAL Words
Lets use Photos/ Imagery to tell the story

We'll need a Banner Menu -
About Us
Expertise
Global Outlook
Sectors
Management
Media
Contact Us

Many thanks
Best wishes
Dennis.

Target Market(s)

Investors
Clients

Coding

Coded - Design and coding required

Number of Pages Required

5+ page

Font styles to use
Sans Serif

Colors
886aae
3176b5
00a990
f68e4d
f04a50
e667a6

Requirements
Must have
• WordPress Coding

Checkout this Website for look and feel - its cool:
www.qvr-example.com

Harbor Crest Partners
(Harbor Crest Holdings LLP)
London
E9 4ZX
United Kingdom

www.HarborCrestPartners-example.com
Nice to have
• Sophisticated colour palette - black/ brown/ blue/ purple/

```html
<!DOCTYPE html>
<html lang="en">
<head>
<meta charset="utf-8">
<title>Harbor Crest — Boutique Investment Company</title>
<link rel="stylesheet" href="https://fonts.googleapis.com/css2?family=Outfit:wght@300;400;500;600;700&family=Mulish:wght@400;500;600;700&display=swap">
<style>
:root{
  --orange:#f68e4d;
  --purple:#886aae;
  --purple-deep:#6f55a0;
  --ink:#1d1d1f;
  --text:#555;
  --grey-bg:#efefef;
  --footer:#191919;
  --white:#fff;
}
*{box-sizing:border-box;margin:0;padding:0}
html,body{width:1200px;height:4290px;overflow:hidden}
body{font-family:"Mulish",sans-serif;color:var(--text);background:var(--white);position:relative}
h1,h2,h3,h4,.brand{font-family:"Outfit",sans-serif;color:var(--ink)}
.rule{display:block;width:46px;height:4px;background:var(--orange);margin-top:18px}
.rule.center{margin-left:auto;margin-right:auto}
.btn{display:inline-block;background:var(--orange);color:#fff;font-family:"Outfit",sans-serif;font-weight:600;font-size:16px;width:182px;height:50px;line-height:50px;text-align:center;border-radius:25px;text-decoration:none}

/* top bar */
.topbar{height:37px;background:var(--orange);color:#fff;font-family:"Outfit",sans-serif;font-weight:600;font-size:15px;display:flex;justify-content:flex-end;align-items:center;gap:56px;padding-right:88px}
.topbar span{display:flex;align-items:center;gap:8px}
/* nav */
.nav{height:86px;display:flex;align-items:center;justify-content:space-between;padding:0 88px 0 88px;border-bottom:1px solid #eee}
.brand{color:var(--purple);font-weight:700;font-size:25px;letter-spacing:.5px}
.nav ul{display:flex;list-style:none;gap:25px;font-family:"Outfit",sans-serif;font-size:15px;color:#333}
.nav li.active{color:var(--orange);font-weight:600}
/* hero */
.hero{height:591px;position:relative;background:
  radial-gradient(ellipse at 20% 80%,rgba(40,140,70,.45),transparent 45%),
  radial-gradient(ellipse at 80% 35%,rgba(30,90,170,.5),transparent 50%),
  linear-gradient(180deg,#0d1a2e,#0a1326);text-align:center;color:#fff}
.hero h1{color:#fff;font-size:92px;font-weight:700;padding-top:210px;line-height:1;letter-spacing:1px}
.hero p{font-family:"Outfit",sans-serif;font-weight:300;font-size:36px;margin-top:6px;letter-spacing:.5px}
/* about */
.about{height:484px;display:flex}
.about .copy{width:626px;padding:68px 0 0 91px}
.about h2{font-size:44px;font-weight:600}
.about p{font-size:15px;line-height:27px;margin-top:28px;width:470px}
.about p+p{margin-top:26px}
.about .btn{margin-top:28px}
.about .visual{flex:1;background:linear-gradient(180deg,#6c7cae 0%,#8a8db6 45%,#c9a47e 80%,#b8b8c4 100%)}
/* sectors */
.sectors{height:844px;background:var(--grey-bg);padding-top:82px;text-align:center}
.sectors h2{font-size:44px;font-weight:600}
.sector-grid{display:grid;grid-template-columns:repeat(3,329px);column-gap:17px;row-gap:50px;margin:38px 0 0 90px}
.sector{position:relative;height:236px}
.sector .photo{height:236px}
.sector .label{position:absolute;left:28px;right:28px;top:206px;height:55px;line-height:55px;background:var(--purple);color:#fff;font-family:"Outfit",sans-serif;font-weight:600;font-size:17px}
/* global outlook */
.outlook{height:551px;display:flex}
.outlook .visual{width:589px;background:linear-gradient(160deg,#d8c6a8 0%,#7fa6c4 40%,#2c5f86 75%,#9fc2d6 100%)}
.outlook .copy{padding:78px 0 0 38px;width:580px}
.outlook h2{font-size:44px;font-weight:600}
.outlook p{font-size:15px;line-height:31.5px;margin-top:28px;text-align:justify}
.outlook .btn{margin-top:24px}
/* management */
.management{height:506px;background:linear-gradient(180deg,#7e62aa,#8a6cb0 60%,#9477b8);text-align:center;color:#fff;padding-top:84px}
.management h2{color:#fff;font-size:44px;font-weight:600}
.management .rule{background:#fff}
.management p{font-size:15px;line-height:34px;width:930px;margin:26px auto 0}
.management .btn{margin-top:24px}
/* media */
.media{height:778px;padding-top:88px;text-align:center}
.media h2{font-size:44px;font-weight:600}
.media-grid{display:grid;grid-template-columns:repeat(3,323px);column-gap:25px;margin:36px 0 0 90px;text-align:left}
.post{height:484px;border-left:9px solid var(--orange);border-bottom:9px solid var(--orange);position:relative;background:#fff;box-shadow:0 2px 10px rgba(0,0,0,.08)}
.post.featured{border-color:var(--purple)}
.post .photo{height:250px}
.post .meta{position:absolute;left:50px;right:50px;top:160px;height:74px;background:var(--orange);color:#fff;font-size:13px;text-align:center;padding-top:14px;line-height:24px;opacity:.95}
.post .avatar{position:absolute;right:12px;top:206px;width:84px;height:84px;border-radius:50%;border:4px solid #fff;background:#d9c2b3}
.post h3{font-size:21px;font-weight:600;line-height:24px;padding:56px 0 0 17px;width:230px}
.post p{font-size:14px;line-height:28px;padding:18px 0 0 17px;width:290px;color:#777}
.post .more{position:absolute;right:10px;bottom:12px;color:var(--orange);font-family:"Outfit",sans-serif;font-weight:600;font-size:15px}
/* footer */
.footer{height:413px;background:var(--footer);color:#fff;position:relative}
.footer .brand{color:#fff;position:absolute;left:90px;top:80px;font-size:25px}
.socials{position:absolute;left:90px;top:128px;display:flex;gap:22px}
.socials span{width:16px;height:16px;background:#fff;border-radius:3px}
.footer h4{color:#fff;font-size:20px;font-weight:600;position:absolute;top:78px}
.footer h4 .rule{width:14px;height:3px;margin-top:12px}
.footer ul{list-style:none;position:absolute;top:148px;font-size:14px;line-height:30.5px}
.copyright{position:absolute;left:0;right:0;top:374px;text-align:center;font-size:12px}
.page-code{position:absolute;right:20px;top:374px;font-size:12px}
</style>
</head>
<body>

<header>
  <div class="topbar">
    <span><svg width="16" height="12" viewBox="0 0 16 12"><rect x="0" y="0" width="16" height="12" rx="1.5" fill="#fff"/><path d="M1 1l7 6 7-6" stroke="#f68e4d" stroke-width="1.5" fill="none"/></svg>info@harborcrest-example.com</span>
    <span><svg width="14" height="14" viewBox="0 0 24 24"><path fill="#fff" d="M6.6 10.8a15.1 15.1 0 006.6 6.6l2.2-2.2c.3-.3.7-.4 1-.2 1.1.4 2.3.6 3.6.6.6 0 1 .4 1 1V20c0 .6-.4 1-1 1A17 17 0 013 4c0-.6.4-1 1-1h3.5c.6 0 1 .4 1 1 0 1.3.2 2.5.6 3.6.1.3 0 .7-.2 1z"/></svg>+0 000 000 000</span>
  </div>
  <nav class="nav">
    <div class="brand">HARBOR CREST</div>
    <ul>
      <li class="active">Home</li><li>About Us</li><li>Expertise</li><li>Global Outlook</li><li>Sectors</li><li>Management</li><li>Media</li><li>Contact Us</li>
    </ul>
  </nav>
</header>

<section class="hero" role="img" aria-label="Dark financial market chart background with glowing green and blue trend lines">
  <h1>Harbor Crest</h1>
  <p>Boutique Investment Company</p>
</section>

<section class="about">
  <div class="copy">
    <h2>About Us</h2>
    <span class="rule"></span>
    <p>Lorem ipsum dolor sit amet, consectetur adipiscing elit, sed do eiusmod tempor incididunt ut labore et dolore magna aliqua. Ut enim ad minim veniam, quis nostrud exercitation</p>
    <p>Duis aute irure dolor in reprehenderit in voluptate velit esse cillum dolore eu fugiat nulla pariatur.</p>
    <a class="btn">Read More</a>
  </div>
  <div class="visual" role="img" aria-label="Businessman looking over a city skyline at dusk beneath a glowing world map"></div>
</section>

<section class="sectors">
  <h2>Sectors</h2>
  <span class="rule center"></span>
  <div class="sector-grid">
    <div class="sector"><div class="photo" role="img" aria-label="Hands handing over house keys" style="background:linear-gradient(135deg,#2a3550,#8a6a50 60%,#e8e2da)"></div><div class="label">Real Estate</div></div>
    <div class="sector"><div class="photo" role="img" aria-label="Online shopping on a laptop and phone" style="background:linear-gradient(135deg,#3a3a3e,#8a8f9a 50%,#d0d3d8)"></div><div class="label">E-Commerce</div></div>
    <div class="sector"><div class="photo" role="img" aria-label="Doctor comforting an elderly patient" style="background:linear-gradient(135deg,#cfd8e0,#a8b8c4 50%,#e6e2dc)"></div><div class="label">Healthcare</div></div>
    <div class="sector"><div class="photo" role="img" aria-label="Hands using a pump bottle of lotion" style="background:linear-gradient(135deg,#f3efec,#e4d6cf 55%,#f6f4f2)"></div><div class="label">Beauty &amp; Personal Care</div></div>
    <div class="sector"><div class="photo" role="img" aria-label="Team around a desk with connected digital devices" style="background:linear-gradient(135deg,#9a9a9a,#d2d2d2 50%,#7a7a7a)"></div><div class="label">Technology</div></div>
    <div class="sector"><div class="photo" role="img" aria-label="Mining site lit at night" style="background:linear-gradient(180deg,#121c44,#1e2d63 55%,#3a4f7a)"></div><div class="label">Resources</div></div>
  </div>
</section>

<section class="outlook">
  <div class="visual" role="img" aria-label="Stacked coins with a rising financial chart overlay"></div>
  <div class="copy">
    <h2>Global Outlook</h2>
    <span class="rule"></span>
    <p>Lorem ipsum dolor sit amet, consectetur adipiscing elit, sed do eiusmod tempor incididunt ut labore et dolore magna aliqua. Ut enim ad minim veniam, quis nostrud exercitation ullamco laboris nisi ut aliquip ex ea commodo consequat. Duis aute irure dolor in reprehenderit in voluptate velit esse cillum dolore eu fugiat nulla pariatur. Excepteur sint occæcat cupidatat non proident, sunt in culpa qui officia deserunt mollit anim id est laborum</p>
    <a class="btn">Read More</a>
  </div>
</section>

<section class="management">
  <h2>Management</h2>
  <span class="rule center"></span>
  <p>Lorem ipsum dolor sit amet, consectetur adipiscing elit, sed do eiusmod tempor incididunt ut labore et dolore magna aliqua. Ut enim ad minim veniam, quis nostrud exercitation ullamco laboris nisi ut aliquip ex ea commodo consequat. Duis aute irure dolor in reprehenderit in voluptate velit esse cillum dolore eu fugiat nulla pariatur. Excepteur sint occæcat cupidatat non proident, sunt in culpa qui officia deserunt mollit anim id est laborum</p>
  <a class="btn">Read More</a>
</section>

<section class="media">
  <h2>Media</h2>
  <span class="rule center"></span>
  <div class="media-grid">
    <article class="post">
      <div class="photo" role="img" aria-label="Hourglass beside stacks of coins" style="background:linear-gradient(135deg,#c9d3de,#8c99a8 55%,#b89a74)"></div>
      <div class="avatar" role="img" aria-label="Author portrait"></div>
      <h3>Lorem ipsum dolor sit amet</h3>
      <p>Lorem ipsum dolor sit met,onsectetur adipiscing elit, sed do eiusmod empor incididunt ut labore et dolore</p>
      <span class="more">Read More</span>
    </article>
    <article class="post featured">
      <div class="photo" role="img" aria-label="Digital target surrounded by business icons" style="background:linear-gradient(135deg,#0e2236,#1c4a66 55%,#0b1826)"></div>
      <div class="meta">Harbor Crest / By Admin<br>Jan25,2020</div>
      <div class="avatar" role="img" aria-label="Author portrait"></div>
      <h3>Lorem ipsum dolor sit amet</h3>
      <p>Lorem ipsum dolor sit met,onsectetur adipiscing elit, sed do eiusmod empor incididunt ut labore et dolore</p>
      <span class="more">Read More</span>
    </article>
    <article class="post">
      <div class="photo" role="img" aria-label="Trading charts on a tablet and monitor" style="background:linear-gradient(135deg,#1a2a40,#3d6288 55%,#8a7460)"></div>
      <div class="avatar" role="img" aria-label="Author portrait"></div>
      <h3>Lorem ipsum dolor sit amet</h3>
      <p>Lorem ipsum dolor sit met,onsectetur adipiscing elit, sed do eiusmod empor incididunt ut labore et dolore</p>
      <span class="more">Read More</span>
    </article>
  </div>
</section>

<footer class="footer">
  <div class="brand">HARBOR CREST</div>
  <div class="socials" aria-label="Social links"><span></span><span></span><span></span><span></span><span></span></div>
  <h4 style="left:450px">Links<span class="rule"></span></h4>
  <ul style="left:451px"><li>Home</li><li>About Us</li><li>Expertise</li><li>Global Outlook</li></ul>
  <ul style="left:721px"><li>Sectors</li><li>Management</li><li>Media</li><li>Contact Us</li></ul>
  <h4 style="left:1005px">Important<span class="rule"></span></h4>
  <ul style="left:1006px"><li>Sign In</li><li>FAQ</li><li>Career</li></ul>
  <div class="copyright">Copyright © 2021 The Company Name.All rights reserved.</div>
  <div class="page-code">C28</div>
</footer>

</body>
</html>
```